Simple Recipe eBook

I need the graphic work done for a simple recipe ebook, I have attached all of the required information for it, as well as our company logo. Further company info can be found at velorabix.com

I would like each recipe page to include 2 recipes, each recipe needs to include ingredients, picture, method, and nutritional info.

I would like the style to appear fresh and healthy, with lots of graphics and colours to match.
Please let me know if you need any guidance

Target Market(s)

Females aged from 15-25

Industry/Entity Type

It Company

```html
<!DOCTYPE html>
<html lang="en">
<head>
<meta charset="utf-8">
<title>Velorabix Recipe eBook – Back Cover</title>
<link rel="stylesheet" href="https://fonts.googleapis.com/css2?family=Lexend:wght@400;600&family=Leckerli+One&display=swap">
<style>
  :root {
    --canvas: #ffffff;
    --wood-light: #e8a94e;
    --wood-dark: #d38a2c;
    --checker: #fbe27f;
    --badge: #ffffff;
    --ink: #4a4546;
    --text: #1d1a17;
    --icon-web: #ec8a2c;
    --icon-social: #3b5a9a;
    --icon-photo: #e2505a;
  }
  * { margin: 0; padding: 0; box-sizing: border-box; }
  html, body {
    width: 1200px; height: 1000px; overflow: hidden;
    background: var(--canvas);
  }
  .canvas { position: relative; width: 1200px; height: 1000px; }

  .wood-frame {
    position: absolute; left: 250px; top: 26px; width: 708px; height: 942px;
    background: linear-gradient(180deg, var(--wood-light), var(--wood-dark) 50%, var(--wood-light));
  }
  .checker-panel {
    position: absolute; left: 285px; top: 26px; width: 638px; height: 895px;
    background: var(--checker);
    border-radius: 0 0 30px 30px;
  }

  .brand-badge {
    position: absolute; left: 453px; top: 225px; width: 300px; height: 300px;
    border-radius: 50%; background: var(--badge);
    display: flex; flex-direction: column; align-items: center; justify-content: center;
  }
  .brand-dot {
    width: 66px; height: 66px; border-radius: 50%; background: var(--ink);
    margin-bottom: 20px;
  }
  .brand-name {
    font-family: "Lexend", sans-serif; font-weight: 400;
    font-size: 30px; letter-spacing: 1.5px; color: var(--ink);
    margin-bottom: 28px;
  }

  .farewell {
    position: absolute; left: 0; width: 1200px; top: 548px;
    text-align: center;
    font-family: "Leckerli One", cursive; font-size: 50px; line-height: 1.2; color: var(--ink);
    transform: translateX(5px) rotate(-8deg);
  }

  .contact-list {
    position: absolute; left: 497px; top: 735px; list-style: none;
    font-family: "Lexend", sans-serif; font-weight: 600; font-size: 16px;
    letter-spacing: 0.4px; color: var(--text);
  }
  .contact-item {
    display: flex; align-items: center; gap: 9px; height: 32px; margin-bottom: 27px;
  }
  .contact-icon { width: 33px; height: 32px; flex: none; }
  .social-circle { width: 32px; height: 32px; border-radius: 50%; background: var(--icon-social); }
  .social-square { width: 32px; height: 32px; background: var(--icon-photo); }
</style>
</head>
<body>
<main class="canvas">
  <div class="wood-frame" role="img" aria-label="Light wooden board texture"></div>
  <div class="checker-panel" role="img" aria-label="Yellow diamond checker pattern"></div>

  <div class="brand-badge">
    <span class="brand-dot"></span>
    <span class="brand-name">VELORABIX</span>
  </div>

  <p class="farewell">Good luck!</p>

  <ul class="contact-list">
    <li class="contact-item">
      <svg class="contact-icon" viewBox="0 0 33 32" aria-hidden="true">
        <rect x="2" y="3" width="29" height="19" rx="1" fill="none" stroke="var(--icon-web)" stroke-width="2.5"/>
        <path d="M2 3 L16.5 14 L31 3" fill="none" stroke="var(--icon-web)" stroke-width="1.5"/>
        <rect x="13" y="23" width="7" height="5" fill="var(--icon-web)"/>
        <rect x="9" y="27" width="15" height="3" fill="var(--icon-web)"/>
      </svg>
      <span>velorabix.com</span>
    </li>
    <li class="contact-item">
      <span class="contact-icon social-circle"></span>
      <span>friendnest.com/velorabix</span>
    </li>
    <li class="contact-item">
      <span class="contact-icon social-square"></span>
      <span>pictolo.com/velorabix</span>
    </li>
  </ul>
</main>
</body>
</html>
```